Business Card Design Project

We need a Business Card for an Mechanical Engineering firm in Singapore. The design should be Modern & Technical looking, yet eye catching.

Our company deals in Cutting Tools & Machine Accessories for the Manufacturing Industries such as Oil & Gas, Aero Space, etc... For more information on our Company, you can either email me or view our website www.torvalen.com.sg.

We are trying to revamp our image to give our consumers a fresh new perspective to our company, so we welcome all ideas.

Industry/Entity Type

Business

Requirements
Must have
• Must incorporate New Company Logo into the card as shown in Uploaded file.

```html
<!DOCTYPE html>
<html lang="en">
<head>
<meta charset="utf-8">
<title>Torvalen Tools – Business Card</title>
<link rel="stylesheet" href="https://fonts.googleapis.com/css2?family=Signika:wght@300;400;600&display=swap">
<style>
  :root {
    --maroon: #981b34;
    --ink: #4a1424;
    --paper: #ffffff;
    --label: #e6b9c3;
    --backdrop: #dfe3e2;
  }
  * { margin: 0; padding: 0; box-sizing: border-box; }
  html, body { width: 1200px; height: 900px; overflow: hidden; }
  body {
    background: var(--backdrop);
    font-family: "Signika", "Trebuchet MS", sans-serif;
    position: relative;
  }
  .card {
    position: absolute;
    left: 279px;
    width: 662px;
    height: 378px;
    background: var(--paper);
    overflow: hidden;
  }
  .card-front { top: 47px; }
  .card-back { top: 476px; }

  .holder-name {
    position: absolute; left: 68px; top: 48px;
    font-size: 33px; font-weight: 400; color: var(--ink);
  }
  .name-rule {
    position: absolute; left: 0; top: 90px;
    width: 462px; height: 5px; background: var(--maroon);
  }
  .holder-title {
    position: absolute; left: 68px; top: 101px;
    font-size: 22px; font-weight: 400; color: var(--ink);
  }

  .info-band {
    position: absolute; left: 0; width: 331px;
    background: var(--maroon); color: var(--paper);
    font-size: 17.5px; line-height: 22px;
    padding-left: 41px;
  }
  .info-band::before, .info-band::after {
    content: ""; position: absolute; top: 0; bottom: 0; width: 22px;
    background: repeating-linear-gradient(to bottom,
      var(--maroon) 0 5px, var(--paper) 5px 8px);
  }
  .info-band::before { left: 0; }
  .info-band::after { right: 0; }
  .contact-band { top: 181px; height: 55px; padding-top: 6px; }
  .address-band { top: 254px; height: 110px; padding-top: 9px; }
  .contact-row { display: flex; }
  .contact-label { width: 67px; color: var(--label); font-weight: 300; }
  .company-name { font-weight: 600; color: var(--label); margin-bottom: 5px; }

  .wordmark {
    position: absolute; left: 361px; top: 222px; width: 272px;
    display: flex; align-items: center; justify-content: center; gap: 10px;
    color: var(--maroon); font-size: 29px; font-weight: 400;
    letter-spacing: 0.5px; white-space: nowrap;
  }
  .wordmark-dot {
    width: 18px; height: 18px; border-radius: 50%; background: var(--maroon);
    flex: none;
  }

  .web-box {
    position: absolute; background: var(--maroon); color: var(--paper);
    display: flex; align-items: center; justify-content: center;
    letter-spacing: 1px;
  }
  .front-web { left: 362px; top: 317px; width: 271px; height: 37px; font-size: 18px; }

  .back-stripes {
    position: absolute; inset: 0;
    background: repeating-linear-gradient(to bottom,
      var(--maroon) 0 7px, var(--paper) 7px 11px);
  }
  .back-clear {
    position: absolute; left: 150px; top: 152px; width: 362px; height: 70px;
    background: var(--paper);
  }
  .back-web {
    left: 160px; top: 160px; width: 342px; height: 54px;
    font-size: 27px; letter-spacing: 2px;
  }
</style>
</head>
<body>
  <section class="card card-front">
    <h1 class="holder-name">Marcus Tan</h1>
    <div class="name-rule"></div>
    <p class="holder-title">President-CEO</p>

    <div class="info-band contact-band">
      <div class="contact-row"><span class="contact-label">mobile</span><span>65-61234567</span></div>
      <div class="contact-row"><span class="contact-label">email</span><span>info@torvalen.com.sg</span></div>
    </div>

    <div class="info-band address-band">
      <p class="company-name">Torvalen Tools Pte Ltd</p>
      <p>27 Kallang Way #03-12</p>
      <p>Kallang Industrial Park</p>
      <p>Singapore 349291</p>
    </div>

    <div class="wordmark"><span class="wordmark-dot"></span>TORVALEN TOOLS</div>
    <div class="web-box front-web">www.torvalen.com.sg</div>
  </section>

  <section class="card card-back">
    <div class="back-stripes"></div>
    <div class="back-clear"></div>
    <div class="web-box back-web">www.torvalen.com.sg</div>
  </section>
</body>
</html>
```